Music Marketing Agency in need of a fully responsive website

Need a website for our music marketing agency with a nice Rev slider has the ability to take payments has a section with our work and client able to see case studies able to download our media kit in PDF can take appointments has social media and a careers upload section. Also want a prominent contact form. Nice and icons for music industry. I want them to be able to download a free Picsandra marketing download Very clean and not large icons or menu at the top very minimal menu bar this will have to go with our logo as well which I will add to order. I want this to be a membership oriented site. so there will be packages displayed or a membership form which they can use to sign up and need a login window. Also need to be able to put Tunevox playlist on the website. Save a section for past clients logos.Again this has to be a clean concept I would like pictures of Quellos such as an app promotion. Definitely want lots of flash words in bold letters across the pages when they scroll through new sections.
Updates

Need extra days to review

Target Market(s)

Urban Music

Coding

Coded - Design and coding required

Font styles to use
Serif

Colors

Designer to choose colors to be used in the design.

Requirements
Must have
• Please Add Logos attached at the Footer

```html
<!DOCTYPE html>
<html lang="en">
<head>
<meta charset="utf-8">
<title>Norvale Sound – Log In</title>
<link rel="stylesheet" href="https://fonts.googleapis.com/css2?family=Montserrat:wght@700&family=Oswald:wght@500&family=Open+Sans:wght@400;600&display=swap">
<style>
  :root {
    --wine: #7a0036;
    --wine-deep: #5e0029;
    --crimson: #d4073f;
    --magenta: #c2125d;
    --accent: #e0004d;
    --white: #ffffff;
    --ink: #2b2b2b;
    --muted: #5f5f5f;
    --field-border: #d2d2d2;
  }
  * { box-sizing: border-box; margin: 0; padding: 0; }
  html, body { width: 1200px; height: 624px; overflow: hidden; }
  body {
    position: relative;
    font-family: "Open Sans", Arial, sans-serif;
    background: var(--wine);
  }
  .backdrop {
    position: absolute; inset: 0;
    background:
      radial-gradient(ellipse 60% 45% at 50% 0%, var(--wine) 0%, rgba(122,0,54,0) 100%),
      linear-gradient(180deg, var(--wine) 0%, var(--wine-deep) 22%, #9a0a3c 55%, var(--crimson) 80%, var(--magenta) 100%);
  }
  .backdrop::after {
    content: ""; position: absolute; inset: 0;
    background: linear-gradient(90deg, rgba(230,20,60,.35) 0%, rgba(0,0,0,0) 30%, rgba(0,0,0,0) 70%, rgba(210,20,110,.35) 100%);
  }
  .brand {
    position: absolute; top: 94px; left: 0; width: 100%;
    text-align: center;
    font-family: "Montserrat", Arial, sans-serif;
    font-weight: 700; font-size: 30px; line-height: 36px; color: var(--white);
    letter-spacing: .3px;
  }
  .login-card {
    position: absolute; left: 315px; top: 167px;
    width: 570px; height: 358px;
    background: var(--white);
  }
  .login-heading {
    position: absolute; top: 37px; left: 0; width: 100%;
    display: flex; justify-content: center; align-items: center; gap: 14px;
  }
  .login-heading svg { width: 54px; height: 54px; display: block; }
  .login-heading h1 {
    font-family: "Oswald", Arial, sans-serif;
    font-weight: 500; font-size: 42px; color: var(--ink);
    line-height: 1; letter-spacing: .5px;
  }
  .field {
    position: absolute; left: 99px; width: 373px; height: 44px;
    border: 1px solid var(--field-border);
    padding: 0 22px;
    font-family: inherit; font-size: 13px; color: var(--muted);
    background: var(--white);
    outline: none;
  }
  .field::placeholder { color: var(--muted); }
  .field-email { top: 122px; }
  .field-password { top: 180px; }
  .submit {
    position: absolute; left: 99px; top: 238px; width: 373px; height: 43px;
    border: none; background: var(--accent); color: var(--white);
    font-family: inherit; font-weight: 600; font-size: 14px; letter-spacing: .5px;
  }
  .forgot {
    position: absolute; top: 302px; left: 0; width: 100%;
    text-align: center; font-size: 13.5px; color: var(--muted); text-decoration: none;
  }
  .site-footer {
    position: absolute; top: 567px; left: 0; width: 100%;
    text-align: center; font-size: 13px; color: var(--white);
  }
  .site-footer a { color: var(--white); text-decoration: none; }
  .site-footer .divider { margin: 0 6px; }
</style>
</head>
<body>
  <div class="backdrop" role="img" aria-label="Background of glowing red and pink equalizer bars rising in perspective"></div>

  <div class="brand">Norvale Sound</div>

  <form class="login-card">
    <div class="login-heading">
      <svg viewBox="0 0 54 54" aria-hidden="true">
        <circle cx="27" cy="27" r="25.5" fill="none" stroke="var(--accent)" stroke-width="2"/>
        <circle cx="27" cy="21" r="6" fill="var(--accent)"/>
        <path d="M16 36 q0-8 11-8 q11 0 11 8 v2 q0 1-1 1 h-20 q-1 0-1-1z" fill="var(--accent)"/>
      </svg>
      <h1>LOG IN</h1>
    </div>
    <input class="field field-email" type="email" placeholder="Email Address">
    <input class="field field-password" type="password" placeholder="Password">
    <button class="submit" type="button">LOG IN</button>
    <a class="forgot" href="#">Forgot Your Password?</a>
  </form>

  <footer class="site-footer">
    Copyright © 2018 NORVALE SOUND - All rights reserved <span class="divider">|</span> <a href="#">Privacy policy</a>
  </footer>
</body>
</html>
```